Business card for Crestline Bathrooms

Please design a business card for our bathroom renovation business. You can use my existing logo, but if you have an idea to modernize it, I would like to see it. Please see attached files first. I would like to use the blue and the orange theme. I like the concept of using the shower head in the logo. Please find following a design (or two) that I have been trying to create with my limited resources. That design was for a sign, but I was going to adopt it and use it as a business card as well. I like the concept of the water splash but I don’t think it “flows” nicely together with the logo. Another thought is that maybe creating the logo out of water splash could work and have a dramatic effect (like the water text and the butterfly picture attached with similar background instead of white). If the above doesn’t work I would like to see a modern simplified design. One of the attached files named as the unwanted business card has all the details that I want included in the business card. Please note that it is two sided.
Updates

I am very thankful for the designs that I have received, but they are very similar and only a couple of attempts to do something with the water splash as per my original brief. Modernizing the logo and having it made out of out of water splash with the orange as color accent could work and have a dramatic effect (like the water text and the butterfly picture attached with similar background instead of white). Please do not use the butterfly itself! This is just an example that images can be created out of water splash.

Contact Information for Business Card

all the details are on the unwonted business card file included

Colors
3176b5

Requirements
Nice to have
• Copied from the brief:
• ... maybe creating the logo out of water splash could work and have a dramatic effect (like the water text and the butterfly picture attached with similar background instead of white). Please do not use the butterfly itself!
Should not have
• I am getting designs with a butterfly. The butterfly picture was an example of creating something from a water splash. The butterfly itself has no association with anything other than the concept of creating a logo out of water splash. Sorry, I thought I was clear in the brief.

```html
<!DOCTYPE html>
<html lang="en">
<head>
<meta charset="utf-8">
<title>Crestline Bathrooms – Business Card</title>
<link href="https://fonts.googleapis.com/css2?family=Roboto+Condensed:wght@700&family=Roboto:wght@400;500&display=swap" rel="stylesheet">
<style>
  :root {
    --page-bg: #e9eaec;
    --card-front-bg: #c9d6e0;
    --card-front-bg-2: #bccbd8;
    --card-back-bg: #f4f4f4;
    --brand-blue: #0e4570;
    --brand-coral: #ef7a6a;
    --text-grey: #4a4f55;
    --badge-grey: #6a6e73;
    --badge-grey-soft: #8d9196;
  }
  html, body {
    margin: 0;
    width: 1200px;
    height: 960px;
    overflow: hidden;
    background: var(--page-bg);
    font-family: "Roboto", Arial, sans-serif;
  }
  .canvas { position: relative; width: 1200px; height: 960px; }

  .card {
    position: absolute;
    width: 598px;
    height: 342px;
    border-radius: 18px;
    overflow: hidden;
    box-shadow: 0 3px 8px rgba(0,0,0,0.18);
  }

  /* Front */
  .card-front {
    left: 322px; top: 108px;
    background: linear-gradient(135deg, var(--card-front-bg), var(--card-front-bg-2));
  }
  .shower-art {
    position: absolute;
    left: 220px; top: 0; right: 0; bottom: 0;
    background:
      radial-gradient(ellipse 95px 75px at 48% 36%, rgba(239,122,106,0.55), rgba(239,122,106,0) 100%),
      radial-gradient(ellipse 200px 190px at 55% 48%, rgba(14,69,112,0.30), rgba(14,69,112,0.12) 60%, rgba(14,69,112,0) 100%);
  }
  .holder-name {
    position: absolute;
    left: 29px; top: 163px;
    margin: 0;
    font-family: "Roboto Condensed", Arial, sans-serif;
    font-weight: 700;
    font-size: 21px;
    color: var(--brand-blue);
    letter-spacing: 0.2px;
  }
  .postal {
    position: absolute;
    left: 29px; top: 202px;
    margin: 0;
    font-size: 14px;
    line-height: 19px;
    color: var(--text-grey);
    font-style: normal;
  }
  .contact-list {
    position: absolute;
    left: 29px; top: 248px;
    margin: 0; padding: 0;
    list-style: none;
    font-size: 14px;
    line-height: 19px;
    color: var(--text-grey);
  }
  .contact-list li { display: flex; align-items: center; gap: 8px; }
  .contact-list svg { width: 14px; height: 14px; fill: var(--brand-blue); flex: none; }

  /* Back */
  .card-back {
    left: 320px; top: 493px;
    background: var(--card-back-bg);
    text-align: center;
  }
  .brand-lockup {
    position: absolute;
    left: 0; right: 0; top: 84px;
    display: flex; justify-content: center; align-items: center; gap: 12px;
  }
  .brand-dot { width: 18px; height: 18px; border-radius: 50%; background: var(--brand-coral); }
  .brand-name { margin: 0; font-size: 34px; font-weight: 500; color: var(--brand-blue); }
  .services {
    position: absolute;
    left: 0; right: 0; top: 187px;
    margin: 0; padding: 0;
    list-style: none;
    font-size: 14px;
    line-height: 18px;
    color: var(--text-grey);
  }
  .memberships {
    position: absolute;
    left: 0; right: 0; top: 274px;
    display: flex; justify-content: center; align-items: center; gap: 16px;
  }
  .badge-round {
    width: 32px; height: 34px;
    border-radius: 8px 8px 14px 14px;
    background: var(--badge-grey);
  }
  .badge-divider { width: 1px; height: 34px; background: var(--badge-grey-soft); }
  .badge-wide {
    width: 116px; height: 26px;
    border-radius: 13px;
    background: var(--badge-grey-soft);
  }
</style>
</head>
<body>
<div class="canvas">

  <section class="card card-front">
    <div class="shower-art" role="img" aria-label="Illustration of a coral shower head on a curving blue hose spraying water, over a water-droplet background"></div>
    <h1 class="holder-name">DANIEL MARSH</h1>
    <address class="postal">PO Box 48<br>Kestrel Vale 2740</address>
    <ul class="contact-list">
      <li><svg viewBox="0 0 24 24"><path d="M6.6 10.8a15.1 15.1 0 0 0 6.6 6.6l2.2-2.2a1 1 0 0 1 1-.25 11.4 11.4 0 0 0 3.6.6 1 1 0 0 1 1 1V20a1 1 0 0 1-1 1A17 17 0 0 1 3 4a1 1 0 0 1 1-1h3.5a1 1 0 0 1 1 1c0 1.25.2 2.45.6 3.6a1 1 0 0 1-.25 1z"/></svg>0400 555 218</li>
      <li><svg viewBox="0 0 24 24"><path d="M7 1h10a2 2 0 0 1 2 2v18a2 2 0 0 1-2 2H7a2 2 0 0 1-2-2V3a2 2 0 0 1 2-2zm0 3v14h10V4zm5 15.5a1.2 1.2 0 1 0 0 2.4 1.2 1.2 0 0 0 0-2.4z"/></svg>5550 1947</li>
      <li><svg viewBox="0 0 24 24"><path d="M2 5h20v14H2zm2 2v.5l8 5 8-5V7zm0 2.9V17h16V9.9l-8 5z"/></svg>daniel@crestlinebathrooms.com.au</li>
      <li><svg viewBox="0 0 24 24"><path d="M12 2a10 10 0 1 0 0 20 10 10 0 0 0 0-20zm-1 17.9A8 8 0 0 1 4.2 10.8L9 15.6v1a2 2 0 0 0 2 2zm6.9-2.5a2 2 0 0 0-1.9-1.4h-1v-3a1 1 0 0 0-1-1H8v-2h2a1 1 0 0 0 1-1V7h2a2 2 0 0 0 2-2v-.4a8 8 0 0 1 2.9 12.8z"/></svg>crestlinebathrooms.com.au</li>
    </ul>
  </section>

  <section class="card card-back">
    <div class="brand-lockup">
      <span class="brand-dot"></span>
      <p class="brand-name">Crestline Bathrooms</p>
    </div>
    <ul class="services">
      <li>Complete Bathroom Renovations &amp; Remodelling</li>
      <li>Highly Skilled &amp; Qualified Tradespeople</li>
      <li>Professional Service From Concept To Completion</li>
      <li>All Work Guaranteed</li>
    </ul>
    <div class="memberships">
      <span class="badge-round" role="img" aria-label="Trade association membership badge"></span>
      <span class="badge-divider"></span>
      <span class="badge-wide" role="img" aria-label="Builders association membership badge"></span>
    </div>
  </section>

</div>
</body>
</html>
```